Veldmark Supplies Business Card

Professional business card that stand out to our potential customers. Front and back with clean modern design

Industry/Entity Type

Oil and gas

Contact Information for Business Card

Name, address, website , office phone and cell number

Requirements
Must have
• Editable files for each employee

```html
<!DOCTYPE html>
<html lang="en">
<head>
<meta charset="utf-8">
<title>Veldmark Supplies Business Card</title>
<link href="https://fonts.googleapis.com/css2?family=Montserrat:wght@400;500;600;800&display=swap" rel="stylesheet">
<style>
  :root {
    --brand-red: #ec2227;
    --brand-blue: #12a9cf;
    --ink: #1d1d1f;
    --paper: #ffffff;
    --backdrop: #e6e6e8;
  }
  * { box-sizing: border-box; margin: 0; padding: 0; }
  html, body {
    width: 1200px; height: 900px; overflow: hidden;
    background: var(--backdrop);
    font-family: "Montserrat", sans-serif;
  }
  .canvas { position: relative; width: 1200px; height: 900px; }
  .card {
    position: absolute; left: 290px; width: 620px; height: 354px;
    border-radius: 22px; overflow: hidden;
    box-shadow: 0 10px 26px rgba(0,0,0,.18);
  }
  .card--front { top: 70px; background: var(--brand-red); }
  .card--back { top: 476px; background: var(--paper); }

  .wordmark { position: absolute; display: flex; align-items: center; gap: 12px; }
  .wordmark__square { flex: none; width: 22px; height: 22px; }
  .wordmark__name { font-weight: 800; letter-spacing: .06em; text-transform: uppercase; }

  .card--front .wordmark { left: 0; right: 0; top: 150px; justify-content: center; }
  .card--front .wordmark__square { background: var(--paper); width: 30px; height: 30px; }
  .card--front .wordmark__name { color: var(--paper); font-size: 34px; }

  .card--back .wordmark { left: 40px; top: 112px; width: 180px; }
  .card--back .wordmark__square { background: var(--brand-red); }
  .card--back .wordmark__name { color: var(--brand-red); font-size: 21px; line-height: 1.15; }
  .wordmark__line { display: block; }

  .accent-lines, .wave { position: absolute; left: 0; top: 0; }

  .details { position: absolute; left: 292px; top: 26px; color: var(--ink); }
  .details__name { color: var(--brand-red); font-weight: 800; font-size: 22px; letter-spacing: .02em; text-transform: uppercase; }
  .details__title { font-size: 13px; font-weight: 500; margin-top: 2px; }
  .details__address { font-size: 12.5px; font-weight: 500; line-height: 1.35; margin-top: 12px; }
  .contact-list { list-style: none; margin-top: 10px; }
  .contact-list__item { display: flex; align-items: center; gap: 8px; font-size: 12px; font-weight: 500; height: 19px; }
  .contact-list__icon { flex: none; width: 15px; height: 15px; background: var(--brand-red); border-radius: 2px; display: flex; align-items: center; justify-content: center; }
  .contact-list__highlight { color: var(--brand-red); }
</style>
</head>
<body>
<main class="canvas">
  <section class="card card--front" aria-label="Card front">
    <div class="wordmark">
      <span class="wordmark__square"></span>
      <span class="wordmark__name">Veldmark Supplies</span>
    </div>
  </section>

  <section class="card card--back" aria-label="Card back">
    <div class="wordmark">
      <span class="wordmark__square"></span>
      <span class="wordmark__name"><span class="wordmark__line">Veldmark</span><span class="wordmark__line">Supplies</span></span>
    </div>

    <svg class="accent-lines" width="620" height="354" viewBox="0 0 620 354" aria-hidden="true">
      <line x1="240" y1="118" x2="262" y2="222" stroke="var(--brand-red)" stroke-width="1.4"/>
      <line x1="252" y1="98" x2="270" y2="190" stroke="var(--brand-red)" stroke-width="1.4"/>
      <line x1="248" y1="76" x2="278" y2="236" stroke="var(--brand-blue)" stroke-width="1.4"/>
    </svg>

    <div class="details">
      <h1 class="details__name">Dana Holloway</h1>
      <p class="details__title">President</p>
      <p class="details__address">482 Harlow Ridge Rd, Ste<br>210, Midland, TX 79705</p>
      <ul class="contact-list">
        <li class="contact-list__item">
          <span class="contact-list__icon"><svg width="10" height="10" viewBox="0 0 10 10"><path d="M2 1l2 2-1 1.3a5 5 0 0 0 2.7 2.7L7 6l2 2-1.2 1.2C4.5 9 1 5.5.8 2.2z" fill="#fff"/></svg></span>
          555-014-2236
        </li>
        <li class="contact-list__item">
          <span class="contact-list__icon"><svg width="10" height="10" viewBox="0 0 10 10"><rect x="2.5" y=".5" width="5" height="9" rx="1" fill="none" stroke="#fff"/></svg></span>
          555-019-7741
        </li>
        <li class="contact-list__item">
          <span class="contact-list__icon"><svg width="10" height="10" viewBox="0 0 10 10"><rect x=".5" y="2" width="9" height="6" fill="none" stroke="#fff"/><path d="M.5 2L5 5.5 9.5 2" fill="none" stroke="#fff"/></svg></span>
          info@example-youremail.com
        </li>
        <li class="contact-list__item">
          <span class="contact-list__icon"><svg width="10" height="10" viewBox="0 0 10 10"><circle cx="5" cy="5" r="4" fill="none" stroke="#fff"/><path d="M1 5h8M5 1c-2 2.5-2 5.5 0 8M5 1c2 2.5 2 5.5 0 8" fill="none" stroke="#fff" stroke-width=".8"/></svg></span>
          <span>www.<span class="contact-list__highlight">example-yourwebsite</span>.com</span>
        </li>
      </ul>
    </div>

    <svg class="wave" width="620" height="354" viewBox="0 0 620 354" aria-hidden="true">
      <path d="M0 300 C200 240 380 300 620 170 L620 354 L0 354 Z" fill="var(--brand-red)"/>
      <path d="M0 294 C200 234 380 294 620 164" fill="none" stroke="var(--brand-blue)" stroke-width="4"/>
    </svg>
  </section>
</main>
</body>
</html>
```